Business cards for a fun web development agency

Hi,I am building a web development agency. You can read about it on the website http://kite-loft.examplehost.com. Basically, I want to focus on free and open source products and stay as far away from the corporate business feeling as possible. I want to build a community so I want the business card to feel fun and approachable (at the risk of professional if need be). I am uploading some of my image assets in various file formats. Feel free to use them or make your own if you want just keeping in theme with the website.
Industry/Entity Type
Building
Contact Information for Business Card
Company Name: Boat ShedWebsite: www.kiteloftdev.example (it's currently in alpha on http://kite-loft.examplehost.com if you want to see the them we are trying to capture)My name is: Banner B. SchaferMy email: banner@boatsheddev.comMy phone: 0431 587 904
Look and feel

```html
<!DOCTYPE html>
<html lang="en">
<head>
<meta charset="utf-8">
<title>Kite Loft – Business Cards</title>
<link rel="stylesheet" href="https://fonts.googleapis.com/css2?family=Arimo:wght@400;700&display=swap">
<style>
  :root {
    --backdrop: #e9e6e1;
    --card-top: #ffffff;
    --card-bottom: #eeeeee;
    --slate: #5a7aa8;
    --slate-dark: #4a6894;
    --teal: #1ba6c8;
    --teal-deep: #0d8db0;
    --band-text: #ffffff;
  }
  * { box-sizing: border-box; margin: 0; padding: 0; }
  html, body {
    width: 1200px; height: 902px; overflow: hidden;
    background: var(--backdrop);
    font-family: "Arimo", Arial, sans-serif;
  }
  .sheet {
    position: relative; width: 1200px; height: 902px;
    display: flex; align-items: center; justify-content: center; gap: 40px;
  }
  .card {
    position: relative; width: 540px; height: 310px;
    border-radius: 22px; overflow: hidden;
    background: linear-gradient(180deg, var(--card-top), var(--card-bottom));
    box-shadow: 0 10px 24px rgba(0,0,0,0.18);
  }
  .wordmark {
    position: absolute; left: 0; right: 0; top: 62px;
    display: flex; align-items: center; justify-content: center; gap: 14px;
    color: var(--slate); font-weight: 400; font-size: 56px; letter-spacing: 1px;
  }
  .wordmark-dot {
    width: 40px; height: 40px; border-radius: 50%; background: var(--teal);
  }
  .band-rule {
    position: absolute; left: 0; right: 0; height: 2px; background: var(--teal);
  }
  .band {
    position: absolute; left: 0; right: 0; bottom: 0;
    background: linear-gradient(180deg, var(--teal), var(--teal-deep));
    color: var(--band-text); font-size: 17px;
  }
  /* front */
  .card--front .band-rule { top: 205px; }
  .card--front .band { top: 213px; padding: 16px 28px; display: flex; justify-content: space-between; }
  .services { list-style: none; display: flex; flex-direction: column; gap: 8px; }
  .services li { display: flex; align-items: center; gap: 9px; }
  .services svg { width: 14px; height: 14px; flex: none; }
  /* back */
  .card--back .wordmark { top: 38px; }
  .holder {
    position: absolute; left: 0; right: 0; top: 120px; text-align: center; color: var(--slate);
  }
  .holder-name { font-weight: 700; font-size: 30px; color: var(--slate-dark); }
  .holder-phone { margin-top: 14px; font-size: 26px; }
  .card--back .band-rule { top: 228px; }
  .card--back .band { top: 236px; padding: 10px 22px; }
  .contact-email { position: absolute; right: 22px; top: 10px; font-size: 15px; }
  .contact-web { position: absolute; left: 22px; bottom: 12px; font-size: 15px; }
</style>
</head>
<body>
<main class="sheet">
  <section class="card card--front" aria-label="Card front">
    <div class="wordmark"><span>KITE LOFT</span><span class="wordmark-dot"></span></div>
    <div class="band-rule"></div>
    <div class="band">
      <ul class="services">
        <li><svg viewBox="0 0 14 14"><path d="M7 0v14M0 7h14M2 2l10 10M12 2L2 12" stroke="#fff" stroke-width="1.4"/></svg>Open Source Software</li>
        <li><svg viewBox="0 0 14 14"><path d="M7 0v14M0 7h14M2 2l10 10M12 2L2 12" stroke="#fff" stroke-width="1.4"/></svg>Web Development For Muggles</li>
      </ul>
      <ul class="services">
        <li><svg viewBox="0 0 14 14"><path d="M7 0v14M0 7h14M2 2l10 10M12 2L2 12" stroke="#fff" stroke-width="1.4"/></svg>Consulting For Developers</li>
      </ul>
    </div>
  </section>

  <section class="card card--back" aria-label="Card back">
    <div class="wordmark"><span>KITE LOFT</span><span class="wordmark-dot"></span></div>
    <div class="holder">
      <p class="holder-name">Corwin T. Aldous</p>
      <p class="holder-phone">0431 587 904</p>
    </div>
    <div class="band-rule"></div>
    <div class="band">
      <p class="contact-email">corwin@kiteloftdev.example</p>
      <p class="contact-web">www.kiteloftdev.example</p>
    </div>
  </section>
</main>
</body>
</html>
```